Business Card Design For Office Furniture Clearance Company

Kestrel Office Clearance - our company name pretty much explains what we do, we clear offices for high end clients, mainly plc's and large international companies.

We require a nice looking business card that displays professionalism but without being too serious.

It would be nice to see just a little more than a conventional boring business card, make sure you add some flare.

Industry/Entity Type

Office Furniture

Contact Information for Business Card

CARD 1

Mark Holloway
Director
mark@kestrelofficeclearance.co.uk
m: 07700 153928

t: 01632 960418
www.kestrelofficeclearance.co.uk

Kestrel Office Clearance
Unit K4 B
2-8 Fenwick Lane
Ashcombe
Wrenford
ZZ9 4QT

clear offices, no charge… simple as that, every time.

CARD 2

Peter Radford
Director
peter@kestrelofficeclearance.co.uk
m: 07700 382615

t: 01632 960418

Kestrel Office Clearance
Unit K4 B
2-8 Fenwick Lane
Ashcombe
Wrenford
ZZ9 4QT

Font styles to use
Sans Serif

Requirements
Must have
• A white background - as we have a blue logo.
Nice to have
• Nice use of the logo - play around with this and dissect it.

```html
<!DOCTYPE html>
<html lang="en">
<head>
<meta charset="utf-8">
<title>Kestrel Office Clearance – Business Cards</title>
<link rel="stylesheet" href="https://fonts.googleapis.com/css2?family=Open+Sans:wght@400;600;700&display=swap">
<style>
  :root {
    --brand-blue: #0878be;
    --card-white: #ffffff;
    --ink: #1c1c1c;
    --stage: #eceef1;
  }
  * { box-sizing: border-box; margin: 0; padding: 0; }
  html, body { width: 1200px; height: 900px; overflow: hidden; }
  body {
    background: var(--stage);
    font-family: "Open Sans", Arial, sans-serif;
    position: relative;
  }
  .card {
    position: absolute;
    border-radius: 16px;
    overflow: hidden;
    box-shadow: 0 6px 18px rgba(0,0,0,0.12);
  }
  .card-front { left: 78px; top: 35px; width: 587px; height: 362px; background: var(--card-white); }
  .card-back { left: 390px; top: 506px; width: 565px; height: 349px; background: var(--brand-blue); }
  .card-art { position: absolute; inset: 0; }
  .brand-name {
    position: absolute;
    font-weight: 700;
    font-size: 21px;
    text-align: center;
    transform: translate(-50%, -50%);
  }
  .card-front .brand-name { left: 294px; top: 100px; color: var(--card-white); }
  .card-back .brand-name { left: 275px; top: 129px; color: var(--brand-blue); }

  .contact-list {
    position: absolute;
    right: calc(587px - 304px);
    top: 222px;
    list-style: none;
    font-size: 15px;
    color: var(--ink);
    text-align: right;
  }
  .contact-list li { height: 24.5px; display: flex; align-items: center; justify-content: flex-end; gap: 8px; }
  .contact-list svg { width: 12px; height: 12px; fill: var(--brand-blue); flex: none; }

  .identity { position: absolute; left: 325px; top: 193px; color: var(--ink); }
  .person-name { font-size: 20px; font-weight: 600; color: var(--brand-blue); line-height: 26px; }
  .person-role { font-size: 15px; line-height: 20px; }
  .company-name { font-size: 19px; font-weight: 600; color: var(--brand-blue); line-height: 26px; margin-top: 12px; }
  .address { font-size: 15.5px; line-height: 21.5px; font-style: normal; }

  .tagline {
    position: absolute;
    left: 0; right: 0; top: 256px;
    text-align: center;
    color: var(--card-white);
    font-weight: 600;
    font-size: 18px;
    line-height: 24px;
  }
</style>
</head>
<body>

<section class="card card-front" aria-label="Business card front">
  <svg class="card-art" viewBox="0 0 587 362" aria-hidden="true">
    <rect class="band" x="0" y="50" width="587" height="100" fill="#0878be"/>
    <circle cx="294" cy="100" r="88" fill="#ffffff"/>
    <circle cx="294" cy="100" r="73" fill="#0878be"/>
  </svg>
  <div class="brand-name">Kestrel</div>

  <ul class="contact-list">
    <li>07700 153928
      <svg viewBox="0 0 12 12"><path d="M3 0h6a1 1 0 0 1 1 1v10a1 1 0 0 1-1 1H3a1 1 0 0 1-1-1V1a1 1 0 0 1 1-1zm.5 1.5v8h5v-8z"/></svg></li>
    <li>01632 960418
      <svg viewBox="0 0 12 12"><path d="M2.5 0.5l2 2.5-1 1.5c.7 1.6 2 2.9 3.5 3.6l1.5-1 2.5 2-1.2 2.1C5 10.8 1.2 7 .4 1.7z"/></svg></li>
    <li>mark@kestrelofficeclearance.co.uk
      <svg viewBox="0 0 12 12"><path d="M0 2h12v1L6 7 0 3zM0 4.3l6 4 6-4V10H0z"/></svg></li>
    <li>www.kestrelofficeclearance.co.uk
      <svg viewBox="0 0 12 12"><circle cx="6" cy="6" r="6"/><path d="M1 6h10M6 1c-2 3-2 7 0 10M6 1c2 3 2 7 0 10" stroke="#fff" stroke-width=".8" fill="none"/></svg></li>
  </ul>

  <div class="identity">
    <p class="person-name">Mark Holloway</p>
    <p class="person-role">Director</p>
    <p class="company-name">Kestrel Office Clearance</p>
    <address class="address">Unit K4 B, 2-8 Fenwick Lane<br>Ashcombe, Wrenford<br>ZZ9 4QT</address>
  </div>
</section>

<section class="card card-back" aria-label="Business card back">
  <svg class="card-art" viewBox="0 0 565 349" aria-hidden="true">
    <rect class="band" x="0" y="81" width="565" height="96" fill="#ffffff"/>
    <circle cx="275" cy="129" r="75" fill="#0878be"/>
    <circle cx="275" cy="129" r="61" fill="#ffffff"/>
  </svg>
  <div class="brand-name">Kestrel</div>
  <p class="tagline">clear offices, no charge…<br>simple as that, every time</p>
</section>

</body>
</html>
```